Corporate Business Card

Very professional, Modern, Not to busy, include phone address email, website
(253) 617-4930, 18761 52nd Avenue S, Kent, WA 98047, martin@plumlinegroup.com, varkoworks.com

Target Market(s)

Manufacturing

Industry/Entity Type

Aero, machining, manufacturing, Off road racing

Contact Information for Business Card

Phone, address email, website

```html
<!DOCTYPE html>
<html lang="en">
<head>
<meta charset="utf-8">
<title>Varko Works – Business Card</title>
<link href="https://fonts.googleapis.com/css2?family=Montserrat:wght@400;500;700;800&display=swap" rel="stylesheet">
<style>
  :root {
    --navy: #15336b;
    --red: #d9252b;
    --white: #ffffff;
    --paper: #f7f7f7;
    --ink: #1c1c22;
    --backdrop: #e6e7ea;
  }
  * { margin: 0; padding: 0; box-sizing: border-box; }
  html, body {
    width: 1200px; height: 900px; overflow: hidden;
    background: var(--backdrop);
    font-family: "Montserrat", Arial, sans-serif;
  }
  .card {
    position: absolute;
    width: 620px; height: 354px;
    border-radius: 22px;
    overflow: hidden;
    box-shadow: 0 10px 30px rgba(0,0,0,0.18);
  }
  /* Back side */
  .card-back {
    left: 290px; top: 60px;
    background: var(--navy);
    display: flex; align-items: center; justify-content: center;
  }
  .card-back .brand-name {
    color: var(--white);
    font-weight: 800;
    font-size: 58px;
    letter-spacing: 1px;
    text-transform: uppercase;
  }
  /* Front side */
  .card-front {
    left: 290px; top: 486px;
    background: var(--paper);
  }
  .card-front .wave {
    position: absolute; left: 0; top: 0;
    width: 620px; height: 354px;
  }
  .card-front .brand {
    position: absolute; left: 30px; top: 88px; width: 230px;
    color: var(--navy);
    font-weight: 800;
    font-size: 34px;
    line-height: 1.05;
    text-transform: uppercase;
    text-align: center;
  }
  .card-front .divider {
    position: absolute; left: 282px; top: 62px;
    width: 1.5px; height: 176px;
    background: var(--navy);
  }
  .contact {
    position: absolute; left: 306px; top: 60px;
    color: var(--ink);
  }
  .contact .person {
    font-weight: 800; font-size: 25px; letter-spacing: 1px;
    color: var(--navy); line-height: 1;
  }
  .contact .person .surname { color: var(--red); }
  .contact .role {
    font-size: 14px; font-weight: 500; margin: 4px 0 12px;
  }
  .contact .address {
    font-size: 14px; line-height: 1.25; margin-bottom: 10px;
  }
  .contact .line {
    display: flex; align-items: center; gap: 8px;
    font-size: 14px; line-height: 1.5;
  }
  .contact .line svg { width: 12px; height: 12px; flex: none; }
  .contact .site .domain { color: var(--navy); }
</style>
</head>
<body>

<section class="card card-back">
  <span class="brand-name">Varko Works</span>
</section>

<section class="card card-front">
  <svg class="wave" viewBox="0 0 620 354" aria-hidden="true">
    <path d="M0 170 C 120 245, 330 320, 620 318 L620 354 L0 354 Z" fill="var(--navy)"/>
    <path d="M230 262 C 380 300, 500 310, 620 304 L620 318 C 500 322, 380 310, 230 262 Z" fill="var(--red)"/>
  </svg>

  <div class="brand">Varko<br>Works</div>
  <div class="divider"></div>

  <div class="contact">
    <div class="person">NOLAN <span class="surname">REYES</span></div>
    <div class="role">Owner</div>
    <div class="address">18761 52nd Avenue S, Kent<br>WA 98047</div>
    <div class="line">
      <svg viewBox="0 0 12 12"><path d="M2.5 1 L4.5 1 L5.3 3.5 L4 4.5 C4.6 5.9 6.1 7.4 7.5 8 L8.5 6.7 L11 7.5 L11 9.5 C11 10.3 10.3 11 9.5 11 C5 11 1 7 1 2.5 C1 1.7 1.7 1 2.5 1 Z" fill="var(--red)"/></svg>
      (253) 617-4930
    </div>
    <div class="line">
      <svg viewBox="0 0 12 12"><rect x="0.5" y="2" width="11" height="8" rx="1" fill="var(--red)"/><path d="M1 2.8 L6 6.5 L11 2.8" stroke="var(--white)" stroke-width="1" fill="none"/></svg>
      martin@plumlinegroup.com
    </div>
    <div class="line site">
      <svg viewBox="0 0 12 12"><circle cx="6" cy="6" r="5" fill="none" stroke="var(--red)" stroke-width="1.2"/><ellipse cx="6" cy="6" rx="2.2" ry="5" fill="none" stroke="var(--red)" stroke-width="1"/><path d="M1 6 H11 M2 3.5 H10 M2 8.5 H10" stroke="var(--red)" stroke-width="0.9"/></svg>
      <span>www.<span class="domain">varkoworks</span>.com</span>
    </div>
  </div>
</section>

</body>
</html>
```